Celvara Health Group Presentation Folder, for Cancer Awareness, VERY COLORFUL AND MODERN

Presentation Folder I know pretty much what i want so it should be very eazy , I have included files from folders I use now rebrand them to my new company they will be fine, no sense re creating the wheel
Full Bleed Size
20.87" x 16.68"
53 x 42.4 cm
6260 x 5004 pixels
Document Trim Size
20.75" x 16.56"
52.7 x 42.1 cm
6225 x 4969 pixels

Low design quality

Industry/Entity Type

Medical

Font styles to use
Serif

Colors

Designer to choose colors to be used in the design.

Requirements
Must have
• really I am not looking for some one to redesign, we like our folder front page and would like to see new word information added., there are two folder front pages to choose from
• So Keep the original front page and redesign the back page and the pockets
• Can Make your Design off of one of the ones I already uploaded
Nice to have
• Keep the same color schemes, Keep the original front page and redesign the back page and the pockets
Should not have
• DO not recreate the front covers, use what I gave you and just rebrand

```html
<!DOCTYPE html>
<html lang="en">
<head>
<meta charset="utf-8">
<title>Celvara Health Group – Presentation Folder</title>
<link href="https://fonts.googleapis.com/css2?family=Raleway:wght@300;400;500;600;700&family=Montserrat:wght@800;900&display=swap" rel="stylesheet">
<style>
:root{
  --backdrop:#7d7d7d;
  --backdrop-light:#a3a3a3;
  --paper:#ffffff;
  --navy:#0d1a52;
  --green:#8dc63f;
  --pink:#f29aab;
  --bar-gray:#6d6e70;
  --body-gray:#555a63;
  --frame-blue:#7fd3ef;
  --die-red:#d2232a;
  --fold-green:#45c06a;
}
*{margin:0;padding:0;box-sizing:border-box}
html,body{width:1096px;height:1200px;overflow:hidden}
body{
  position:relative;
  background:radial-gradient(ellipse at 50% 45%,var(--backdrop-light),var(--backdrop));
  font-family:"Raleway",Arial,sans-serif;
  color:var(--navy);
}
.dieline{position:absolute;left:0;top:0}
.abs{position:absolute}

/* inside spread */
.panel-frame{position:absolute;border:1px solid var(--frame-blue)}
.photo{position:absolute;box-shadow:3px 6px 10px rgba(0,0,0,.35)}
.photo--beach{left:128px;top:170px;width:382px;height:236px;transform:rotate(-5deg);
  background:linear-gradient(180deg,#2f7fd0 0%,#6fb3e8 52%,#e9e0cc 60%,#d8cbb0 100%)}
.photo--table{left:598px;top:250px;width:374px;height:244px;transform:rotate(5deg);
  background:linear-gradient(160deg,#f4f2ee 0%,#d9c7a9 45%,#b58d5e 75%,#8c6a45 100%)}
.ribbon{position:absolute;border-radius:40% 40% 10% 10%;
  background:linear-gradient(135deg,#4fb3ee 0%,#4fb3ee 45%,#e35fc7 55%,#e35fc7 100%)}
.ribbon--left{left:446px;top:106px;width:42px;height:66px;transform:rotate(18deg)}
.ribbon--right{left:918px;top:194px;width:44px;height:66px;transform:rotate(18deg)}

.intro-copy{left:124px;top:478px;width:378px;font-size:9.3px;line-height:11.2px;color:var(--navy)}
.intro-copy strong{font-weight:700}
.intro-tagline{left:124px;top:538px;width:390px;font-size:10px;line-height:12px;font-weight:500;color:var(--navy)}

.title-band{left:548px;top:88px;width:494px;height:36px;background:var(--pink);
  color:#fff;font-size:20px;font-weight:600;letter-spacing:2.2px;text-align:center;line-height:36px}
.subhead{left:564px;top:135px;width:425px;text-align:center;font-size:13px;font-weight:500;color:#111}
.subcopy{left:590px;top:160px;width:374px;text-align:center;font-size:10.4px;line-height:12.2px;color:var(--body-gray)}
.tag-bar{left:548px;top:533px;width:494px;height:32px;background:var(--bar-gray);
  color:#fff;font-weight:300;font-size:15px;line-height:32px;padding-left:126px}
.mark-circle{position:absolute;border-radius:50%;background:var(--paper);border:2px solid var(--navy)}
.mark-circle--bar{left:615px;top:544px;width:40px;height:40px}
.bar-name{left:660px;top:570px;font-size:9px;font-weight:700;color:var(--navy)}

/* pockets */
.pocket-frame{position:absolute;width:390px;height:182px;border:1px solid var(--frame-blue);border-top-right-radius:34px}
.pocket-frame--flip{transform:rotate(180deg)}
.pocket-frame--white{border-top-right-radius:0;border-top-left-radius:34px}
.pocket-copy{position:absolute;left:25px;top:24px;width:330px;color:#fff;font-size:5.7px;line-height:6.9px}
.pocket-copy p+p{margin-top:5px}
.pocket-headline{position:absolute;left:25px;top:110px;width:340px;font-family:"Montserrat",Arial,sans-serif;
  font-weight:800;font-size:14px;line-height:16.5px;color:#fff}
.pocket-headline span{color:var(--green)}

.brand-lockup{position:absolute;left:120px;top:72px;display:flex;align-items:center;gap:6px}
.mark-circle--pocket{position:relative;width:38px;height:38px}
.brand-lockup__name{font-size:13px;line-height:13px;font-weight:700;color:var(--navy);letter-spacing:.5px;width:80px}
.brand-name{position:absolute;left:0;width:390px;top:132px;text-align:center;font-family:"Montserrat",Arial,sans-serif;
  font-weight:800;font-size:19px;color:var(--navy)}
.brand-division{position:absolute;left:0;width:390px;top:156px;text-align:center;font-size:7.5px;color:var(--navy)}
.card-slit{position:absolute;width:44px;height:1px;background:var(--die-red)}
</style>
</head>
<body>

<svg class="dieline" width="1096" height="1200" viewBox="0 0 1096 1200" aria-hidden="true">
  <defs>
    <filter id="sheet-shadow" x="-5%" y="-5%" width="110%" height="115%">
      <feDropShadow dx="0" dy="3" stdDeviation="3" flood-opacity=".35"/>
    </filter>
  </defs>
  <g filter="url(#sheet-shadow)">
    <!-- main spread -->
    <path d="M54,60 L62,53 L1036,53 L1042,60 L1042,395 A18,18 0 0 0 1042,432 L1042,616 L1034,624 L62,624 L54,616 L54,432 A18,18 0 0 0 54,395 Z" fill="#fff" stroke="#d2232a" stroke-width=".8"/>
    <!-- upper pockets -->
    <path d="M93,624 L523,624 L492,806 Q486,840 462,840 L93,840 Z" fill="#fff" stroke="#d2232a" stroke-width=".8"/>
    <path d="M552,624 L1004,624 L1004,840 L598,840 Q578,840 574,815 Z" fill="#0d1a52" stroke="#d2232a" stroke-width=".8"/>
    <!-- lower pockets -->
    <path d="M93,896 L490,896 Q520,896 524,930 L544,1112 L93,1112 Z" fill="#0d1a52" stroke="#d2232a" stroke-width=".8"/>
    <path d="M1004,896 L612,896 Q588,896 583,928 L546,1112 L1004,1112 Z" fill="#fff" stroke="#d2232a" stroke-width=".8"/>
  </g>
  <!-- fold lines -->
  <line x1="548" y1="53" x2="548" y2="624" stroke="#45c06a" stroke-width=".8" stroke-dasharray="3 2"/>
  <line x1="93" y1="624" x2="1004" y2="624" stroke="#45c06a" stroke-width=".8" stroke-dasharray="3 2"/>
  <line x1="93" y1="1112" x2="1004" y2="1112" stroke="#45c06a" stroke-width=".8" stroke-dasharray="3 2"/>
  <line x1="545" y1="896" x2="545" y2="1112" stroke="#45c06a" stroke-width=".8" stroke-dasharray="3 2"/>
</svg>

<!-- left inside panel -->
<div class="panel-frame" style="left:107px;top:67px;width:424px;height:542px"></div>
<div class="photo photo--beach" role="img" aria-label="Photo: a multigenerational family walking hand in hand on a sunny beach"></div>
<div class="ribbon ribbon--left" role="img" aria-label="Pink and blue awareness ribbon"></div>
<p class="abs intro-copy"><strong>Hereditary cancer screening</strong> provides vital information to help people with a strong personal or family history of cancer understand their own risk of developing the disease. With this information, they can take steps to Potentially Prevent Cancer, Delay the Onset of Cancer or Catch it at an Earlier stage when outcomes and survival rates are Better.</p>
<p class="abs intro-tagline">Don’t be Afraid of the Answer: Knowledge is Power and Power Eradicates Fear.<br>When You are Fearless, You Will Make all the Right Choices!</p>

<!-- right inside panel -->
<div class="panel-frame" style="left:564px;top:67px;width:425px;height:542px"></div>
<div class="abs title-band">HEREDITARY CANCER SCREENING</div>
<p class="abs subhead">Doctors are the Gatekeepers to Genetic Testing.</p>
<p class="abs subcopy">We have an obligation to help patients understand genetic risk and how testing can guide heath care decisions.</p>
<div class="photo photo--table" role="img" aria-label="Photo: three generations of a family sharing a meal at an outdoor table"></div>
<div class="ribbon ribbon--right" role="img" aria-label="Pink and blue awareness ribbon"></div>
<div class="abs tag-bar">The test you order FOR your patients</div>
<div class="mark-circle mark-circle--bar"></div>
<div class="abs bar-name">Celvara Health Group</div>

<!-- upper left pocket (inverted brand pocket) -->
<div class="pocket-frame pocket-frame--white pocket-frame--flip" style="left:122px;top:641px">
  <div class="card-slit" style="left:138px;top:48px;transform:rotate(45deg)"></div>
  <div class="card-slit" style="left:138px;top:112px;transform:rotate(-45deg)"></div>
  <div class="card-slit" style="left:292px;top:48px;transform:rotate(-45deg)"></div>
  <div class="card-slit" style="left:292px;top:112px;transform:rotate(45deg)"></div>
  <div class="brand-lockup"><div class="mark-circle mark-circle--pocket"></div><div class="brand-lockup__name">CELVARA HEALTH GROUP</div></div>
  <div class="brand-name">Celvara Health Group</div>
  <div class="brand-division">a division of Meridane Medical Sales LLC</div>
</div>

<!-- upper right pocket (inverted message pocket) -->
<div class="pocket-frame pocket-frame--flip" style="left:573px;top:641px">
  <div class="pocket-copy">
    <p>There are many benefits to getting tested, regardless of the eventual result. If one of your family members — however distant — had cancer, there is a chance that you inherited a gene mutation that not only increases your personal risk of cancer, but also could be passed to the next generation. Those who are carriers of hereditary cancer gene mutations, could be at risk of getting cancer earlier in life than the general population. The sooner genetic testing is done, the more likely it is that the risk can be managed appropriately.</p>
    <p>Hereditary cancer screening provides vital information to help people with a strong personal or family history of cancer understand their own risk of developing the disease. With this information, they can take steps to Potentially Prevent Cancer, Delay the Onset of Cancer or Catch it at an Earlier stage when outcomes and survival rates are Better.</p>
  </div>
  <div class="pocket-headline">Identifying an inherited genetic mutation has the potential to prevent cancer <span>and save lives.</span></div>
</div>

<!-- lower left pocket (message) -->
<div class="pocket-frame" style="left:132px;top:912px">
  <div class="pocket-copy">
    <p>There are many benefits to getting tested, regardless of the eventual result. If one of your family members — however distant — had cancer, there is a chance that you inherited a gene mutation that not only increases your personal risk of cancer, but also could be passed to the next generation. Those who are carriers of hereditary cancer gene mutations, could be at risk of getting cancer earlier in life than the general population. The sooner genetic testing is done, the more likely it is that the risk can be managed appropriately.</p>
    <p>Hereditary cancer screening provides vital information to help people with a strong personal or family history of cancer understand their own risk of developing the disease. With this information, they can take steps to Potentially Prevent Cancer, Delay the Onset of Cancer or Catch it at an Earlier stage when outcomes and survival rates are Better.</p>
  </div>
  <div class="pocket-headline">Identifying an inherited genetic mutation has the potential to prevent cancer <span>and save lives.</span></div>
</div>

<!-- lower right pocket (brand) -->
<div class="pocket-frame pocket-frame--white" style="left:583px;top:912px">
  <div class="card-slit" style="left:100px;top:48px;transform:rotate(-45deg)"></div>
  <div class="card-slit" style="left:100px;top:112px;transform:rotate(45deg)"></div>
  <div class="card-slit" style="left:254px;top:48px;transform:rotate(45deg)"></div>
  <div class="card-slit" style="left:254px;top:112px;transform:rotate(-45deg)"></div>
  <div class="brand-lockup" style="left:150px"><div class="mark-circle mark-circle--pocket"></div><div class="brand-lockup__name">CELVARA HEALTH GROUP</div></div>
  <div class="brand-name">Celvara Health Group</div>
  <div class="brand-division">a division of Meridane Medical Sales LLC</div>
</div>

</body>
</html>
```